Business cards for a fun web development agency

Hi,I am building a web development agency. You can read about it on the website http://kite-loft.examplehost.com. Basically, I want to focus on free and open source products and stay as far away from the corporate business feeling as possible. I want to build a community so I want the business card to feel fun and approachable (at the risk of professional if need be). I am uploading some of my image assets in various file formats. Feel free to use them or make your own if you want just keeping in theme with the website.
Industry/Entity Type
Building
Contact Information for Business Card
Company Name: Boat ShedWebsite: www.kiteloftdev.example (it's currently in alpha on http://kite-loft.examplehost.com if you want to see the them we are trying to capture)My name is: Banner B. SchaferMy email: banner@boatsheddev.comMy phone: 0431 587 904
Look and feel

```html
<!DOCTYPE html>
<html lang="en">
<head>
<meta charset="utf-8">
<title>Kite Loft — Business Cards</title>
<link rel="stylesheet" href="https://fonts.googleapis.com/css2?family=Arimo:wght@400&display=swap">
<style>
  :root {
    --bg: #ece8e2;
    --card: #ffffff;
    --card-shade: #f1f2f3;
    --teal: #1fa3c4;
    --navy: #3d6a9a;
    --ink: #4a5560;
  }
  * { margin: 0; padding: 0; box-sizing: border-box; }
  html, body { width: 1200px; height: 885px; overflow: hidden; }
  body {
    background: var(--bg);
    font-family: "Arimo", Arial, sans-serif;
    display: flex;
    align-items: center;
    justify-content: center;
    gap: 50px;
  }
  .card {
    width: 540px;
    height: 310px;
    border-radius: 14px;
    background: linear-gradient(160deg, var(--card) 40%, var(--card-shade));
    box-shadow: 0 6px 18px rgba(0,0,0,0.18);
    position: relative;
    overflow: hidden;
  }
  .wordmark {
    color: var(--navy);
    font-weight: 400;
    letter-spacing: 2px;
    display: flex;
    align-items: center;
    gap: 12px;
    white-space: nowrap;
  }
  .wordmark-dot {
    border-radius: 50%;
    background: currentColor;
    flex: none;
  }
  /* Front */
  .card-front .wordmark {
    position: absolute;
    top: 56px;
    left: 0; right: 0;
    justify-content: center;
    font-size: 48px;
  }
  .card-front .wordmark-dot { width: 40px; height: 40px; }
  .name-rule {
    position: absolute;
    top: 150px;
    left: 0; right: 0;
    display: flex;
    align-items: center;
    gap: 10px;
    color: var(--teal);
    font-size: 21px;
  }
  .name-rule::before, .name-rule::after {
    content: "";
    height: 1px;
    background: var(--teal);
    flex: 1;
  }
  .name-rule::before { flex: 0 0 150px; }
  .contact {
    position: absolute;
    top: 186px;
    left: 160px;
    color: var(--ink);
    font-size: 17px;
    line-height: 1.25;
    list-style: none;
  }
  .accent-band {
    position: absolute;
    left: 0; right: 0; bottom: 0;
    height: 26px;
    background: var(--teal);
  }
  /* Back */
  .card-back { display: flex; align-items: center; justify-content: center; }
  .card-back .wordmark { color: var(--teal); font-size: 54px; }
  .card-back .wordmark-dot { width: 48px; height: 48px; }
</style>
</head>
<body>
  <section class="card card-front" aria-label="Business card front">
    <div class="wordmark">KITE<span class="wordmark-dot"></span>LOFT</div>
    <div class="name-rule">Corwin T. Aldous</div>
    <ul class="contact">
      <li>0431 587 904</li>
      <li>corwin@kiteloftdev.example</li>
      <li>www.kiteloftdev.example</li>
    </ul>
    <div class="accent-band"></div>
  </section>
  <section class="card card-back" aria-label="Business card back">
    <div class="wordmark">KITE<span class="wordmark-dot"></span>LOFT</div>
  </section>
</body>
</html>
```